Flyer-Design für Naturkosmetik und Wellness
Zielgruppe
Naturkosmetik und Wellness
Aufgabenstellung
Das Design soll schlicht sein , aber nicht unscheinbar wirken. Ich möchte die Flyer gerne als Postkarte vorne und hinten gestaltet.
Vorderseite : Mein Name im gleichen Design , wie bei meinen Visitenkarten.Text:Kosmetik und Entspannung im Einklang mit der Natur .
Rückseite : Termine nach Vereinbarung Mo 16.00 h- 19.00h , Mi und Do 15.00h - 19.00h und Fr 14.00h - 18.00h

```html
<!DOCTYPE html>
<html lang="de">
<head>
<meta charset="utf-8">
<title>Kosmetik und Entspannung – Postkarte</title>
<link href="https://fonts.googleapis.com/css2?family=Montserrat:wght@300;400;600;700&display=swap" rel="stylesheet">
<style>
  :root {
    --bg: #dcdcdc;
    --towel-light: #ece8e2;
    --towel-mid: #d9d2c8;
    --towel-dark: #c8bfb2;
    --band: rgba(150, 135, 115, 0.82);
    --brown: #6b5e4f;
    --grey-head: #8c8f93;
    --grey-text: #9a9ca0;
    --white: #ffffff;
  }
  * { margin: 0; padding: 0; box-sizing: border-box; }
  html, body { width: 1200px; height: 2400px; overflow: hidden; }
  body {
    background: var(--bg);
    font-family: "Montserrat", Arial, sans-serif;
    position: relative;
  }
  .card {
    position: absolute;
    left: 120px;
    width: 960px;
    height: 684px;
    overflow: hidden;
  }
  .card--front { top: 440px; }
  .card--back {
    top: 1244px;
    background: var(--white);
    border: 7px solid var(--brown);
  }
  .front__photo {
    position: absolute; inset: 0;
    background:
      radial-gradient(ellipse at 55% 80%, #f2efea 0%, transparent 35%),
      radial-gradient(ellipse at 65% 10%, #eeeae4 0%, transparent 40%),
      linear-gradient(135deg, var(--towel-light) 0%, var(--towel-mid) 50%, var(--towel-dark) 100%);
  }
  .front__band {
    position: absolute;
    left: 62px; top: 246px;
    width: 842px; height: 246px;
    background: var(--band);
    display: flex; flex-direction: column;
    align-items: center; justify-content: center;
    color: var(--white);
    text-align: center;
  }
  .front__title {
    font-weight: 600;
    font-size: 40px;
    letter-spacing: 0.5px;
  }
  .front__subtitle {
    font-weight: 400;
    font-size: 28px;
    letter-spacing: 0.5px;
    margin-top: 4px;
  }
  .front__url {
    position: absolute;
    left: 0; right: 0; top: 606px;
    text-align: center;
    font-size: 26px;
    letter-spacing: 1px;
    color: var(--brown);
  }
  .back__heading {
    position: absolute; left: 0; right: 0; top: 250px;
    text-align: center;
    font-weight: 600;
    font-size: 30px;
    color: var(--grey-head);
  }
  .back__hours {
    position: absolute; left: 0; right: 0; top: 306px;
    text-align: center;
    font-weight: 600;
    font-size: 22px;
    color: var(--grey-text);
    word-spacing: 1px;
  }
  .contact {
    position: absolute;
    top: 424px;
    display: flex;
    align-items: flex-start;
    gap: 14px;
    font-size: 22px;
    color: var(--grey-text);
    line-height: 1.5;
  }
  .contact--address { left: 80px; }
  .contact--reach { left: 520px; flex-direction: column; gap: 4px; }
  .contact__row { display: flex; align-items: center; gap: 14px; }
  .icon { width: 26px; height: 26px; fill: var(--grey-text); flex-shrink: 0; }
  .contact--address .icon { margin-top: 6px; }
</style>
</head>
<body>
  <section class="card card--front">
    <div class="front__photo" role="img" aria-label="Weiche helle Frotteehandtücher in Beige- und Cremetönen"></div>
    <div class="front__band">
      <p class="front__title">KOSMETIK UND ENTSPANNUNG</p>
      <p class="front__subtitle">IM EINKLANG MIT DER NATUR</p>
    </div>
    <p class="front__url">WWW.SEELENRUH.DE</p>
  </section>

  <section class="card card--back">
    <h2 class="back__heading">TERMINE NACH VEREINBARUNG</h2>
    <p class="back__hours">Mo 16.00 h- 19.00h &nbsp;/&nbsp; Mi und Do 15.00h - 19.00h &nbsp;/&nbsp; und Fr 14.00h - 18.00h</p>

    <div class="contact contact--address">
      <svg class="icon" viewBox="0 0 24 24" aria-hidden="true"><path d="M12 2a7 7 0 0 0-7 7c0 5 7 13 7 13s7-8 7-13a7 7 0 0 0-7-7zm0 9.5A2.5 2.5 0 1 1 12 6.5a2.5 2.5 0 0 1 0 5z"/></svg>
      <p>Sabine Korth , Lindenweg 12<br>73525 Waldstetten</p>
    </div>

    <div class="contact contact--reach">
      <div class="contact__row">
        <svg class="icon" viewBox="0 0 24 24" aria-hidden="true"><path d="M3 5h18v14H3z" fill="none" stroke="#9a9ca0" stroke-width="2"/><path d="M3 5l9 8 9-8" fill="none" stroke="#9a9ca0" stroke-width="2"/></svg>
        <span>sabine@seelenruh.de</span>
      </div>
      <div class="contact__row">
        <svg class="icon" viewBox="0 0 24 24" aria-hidden="true"><path d="M6.6 10.8a15 15 0 0 0 6.6 6.6l2.2-2.2a1 1 0 0 1 1-.25 11.4 11.4 0 0 0 3.6.57 1 1 0 0 1 1 1V20a1 1 0 0 1-1 1A17 17 0 0 1 3 4a1 1 0 0 1 1-1h3.5a1 1 0 0 1 1 1c0 1.25.2 2.45.57 3.6a1 1 0 0 1-.25 1z"/></svg>
        <span>Tel. 015120478316</span>
      </div>
    </div>
  </section>
</body>
</html>
```